business card - Helicopter Flight Services, Flight School, etc.

We need a business card design for a new helicopter service.

We offer Helicopter Flight Services, Aerial Filming & Photography, Flight School, and Helicopter Tours. In that order.

Summit BladeAir, Inc.
Dennis Tollerby
SummitBladeair@Kestmail.com
626-418-7352

Based at the Brenwick Airport in Van Nuys, CA. The final design should communicate integrity and safety. Pictures or logos at your discretion.

Card back side - surprise me.

```html
<!DOCTYPE html>
<html lang="en">
<head>
<meta charset="utf-8">
<title>Summit BladeAir, Inc. – Business Card</title>
<link rel="stylesheet" href="https://fonts.googleapis.com/css2?family=Old+Standard+TT:wght@700&family=Open+Sans:wght@400&display=swap">
<style>
  :root {
    --page: #e9e8e4;
    --card: #ffffff;
    --ink: #2b2b2e;
    --ink-soft: #4a4a50;
    --rule: #3a3a3a;
    --band-light: #cfd2ec;
    --band-dark: #6c79c4;
    --icon: #7b86c9;
    --sky-top: #4f8fd0;
    --sky-mid: #8fb9e2;
    --sea: #5f86b4;
    --city: #8b8a86;
    --veil: rgba(255, 255, 255, 0.62);
    --tagline: #4f5866;
  }
  * { box-sizing: border-box; margin: 0; padding: 0; }
  html, body {
    width: 1200px; height: 892px; overflow: hidden;
    background: var(--page);
  }
  .sheet {
    width: 1200px; height: 892px;
    display: flex; flex-direction: column;
    align-items: center; justify-content: center; gap: 50px;
  }
  .card {
    position: relative;
    width: 640px; height: 366px;
    background: var(--card);
    overflow: hidden;
    box-shadow: 0 2px 10px rgba(0, 0, 0, 0.12);
  }
  /* Front: contact side */
  .company {
    position: absolute; right: 30px; top: 26px;
    font-family: "Old Standard TT", Georgia, serif;
    font-weight: 700; font-size: 42px; color: var(--ink);
    letter-spacing: 0.5px;
  }
  .title-rule {
    position: absolute; left: 30px; right: 30px; top: 92px;
    height: 1px; background: var(--rule);
  }
  .person {
    position: absolute; left: 42px; top: 118px;
    font-family: "Open Sans", Arial, sans-serif;
    font-size: 20px; color: var(--ink-soft);
  }
  .divider {
    position: absolute; left: 226px; top: 150px;
    width: 1px; height: 110px; background: var(--rule);
  }
  .contact {
    position: absolute; left: 248px; top: 150px;
    list-style: none;
    font-family: "Open Sans", Arial, sans-serif;
    font-size: 17px; line-height: 25px; color: var(--ink);
  }
  .contact li { display: flex; align-items: center; gap: 10px; white-space: nowrap; }
  .contact .icon { width: 14px; height: 14px; flex: none; }
  .contact .no-icon { padding-left: 24px; }
  .band {
    position: absolute; left: 0; right: 0; bottom: 0; height: 72px;
    background: linear-gradient(90deg, var(--band-light), var(--band-dark));
  }
  /* Back: photo side */
  .photo {
    position: absolute; inset: 0;
    background: linear-gradient(180deg, var(--sky-top) 0%, var(--sky-mid) 40%, var(--sea) 70%, var(--city) 100%);
  }
  .name-strip {
    position: absolute; left: 0; right: 0; top: 148px; height: 92px;
    background: var(--veil);
    padding: 0 28px 0 86px;
  }
  .name-strip .brand {
    font-family: "Old Standard TT", Georgia, serif;
    font-weight: 700; font-size: 46px; color: var(--ink);
    line-height: 56px; padding-top: 2px;
  }
  .name-strip .services {
    font-family: "Open Sans", Arial, sans-serif;
    font-size: 15px; color: var(--tagline);
    text-align: right; white-space: nowrap; line-height: 26px;
  }
</style>
</head>
<body>
<main class="sheet">
  <section class="card card-front">
    <h1 class="company">Summit BladeAir, Inc.</h1>
    <div class="title-rule"></div>
    <p class="person">Dennis Tollerby</p>
    <div class="divider"></div>
    <ul class="contact">
      <li>
        <svg class="icon" viewBox="0 0 14 14" aria-hidden="true"><rect width="14" height="14" fill="var(--icon)"/><path d="M4 3.5c.6 2.8 2.7 5.6 6 6.8l.9-1.4-1.7-1-.8.8c-1.1-.6-2-1.6-2.6-2.7l.8-.8-1-1.7z" fill="#fff"/></svg>
        626-418-7352
      </li>
      <li>
        <svg class="icon" viewBox="0 0 14 14" aria-hidden="true"><rect width="14" height="14" fill="var(--icon)"/><rect x="3" y="4.5" width="8" height="5.5" fill="none" stroke="#fff"/><path d="M3 4.5l4 3 4-3" fill="none" stroke="#fff"/></svg>
        SummitBladeair@Kestmail.com
      </li>
      <li>
        <svg class="icon" viewBox="0 0 14 14" aria-hidden="true"><rect width="14" height="14" fill="var(--icon)"/><path d="M7 11.5C5 9 4.3 7.6 4.3 6.2a2.7 2.7 0 0 1 5.4 0c0 1.4-.7 2.8-2.7 5.3z" fill="#fff"/><circle cx="7" cy="6.2" r="1" fill="var(--icon)"/></svg>
        Brenwick Airport, 4870 Alder Crest Ave.
      </li>
      <li class="no-icon">Ste B, Van Nuys, CA 91406</li>
    </ul>
    <div class="band"></div>
  </section>

  <section class="card card-back">
    <div class="photo" role="img" aria-label="Photo of a white helicopter flying over a coastal city under a blue sky"></div>
    <div class="name-strip">
      <p class="brand">Summit BladeAir, Inc.</p>
      <p class="services">Flight Services · Aerial Filming &amp; Photography · Flight School · Tours</p>
    </div>
  </section>
</main>
</body>
</html>
```